BildeVOLD buisnesscard

Hey :) I need a modern buisnesscard for my company BildeVOLD
It most have:
Dagligleder og Fotograf: Henrik Audun Strandvik

Mob: +4791264085
Epost: post@bildevold.example
Adresse: Kvernbakken9, 6040 Langevåg

Facbook and instagram logo with text BildeVOLD

BildeVOLD logo

It Company

```html
<!DOCTYPE html>
<html lang="en">
<head>
<meta charset="utf-8">
<title>BildeVOLD business card</title>
<link href="https://fonts.googleapis.com/css2?family=Khand:wght@600&family=Roboto:wght@400;500&display=swap" rel="stylesheet">
<style>
  :root {
    --backdrop: #e8e8e8;
    --card-front-top: #b9babc;
    --card-front-bottom: #8c8e91;
    --card-back: #f6f6f6;
    --ink: #8a8b8d;
    --ink-soft: #949596;
    --on-dark: #f4f4f4;
  }
  * { box-sizing: border-box; margin: 0; padding: 0; }
  html, body {
    width: 1200px; height: 576px; overflow: hidden;
    background: var(--backdrop);
    font-family: "Roboto", Arial, sans-serif;
  }
  .canvas { position: relative; width: 1200px; height: 576px; }
  .card {
    position: absolute; top: 139px; width: 484px; height: 294px;
    border-radius: 8px;
    box-shadow: 0 2px 4px rgba(0,0,0,.22);
  }
  .card-front {
    left: 82px;
    background: linear-gradient(180deg, var(--card-front-top), var(--card-front-bottom));
    display: flex; align-items: center; justify-content: center;
  }
  .brand-name-front {
    font-family: "Roboto", Arial, sans-serif;
    font-weight: 500; font-size: 40px; letter-spacing: .5px;
    color: var(--on-dark);
  }
  .card-back { left: 602px; background: var(--card-back); color: var(--ink); }
  .brand-name-back {
    position: absolute; right: 28px; top: 52px;
    font-family: "Roboto", Arial, sans-serif;
    font-weight: 500; font-size: 24px; color: var(--ink);
  }
  .website {
    position: absolute; right: 28px; top: 185px;
    font-size: 12.5px; color: var(--ink-soft);
  }
  .person { position: absolute; left: 23px; top: 151px; }
  .person-name {
    font-family: "Khand", "Arial Narrow", sans-serif;
    font-weight: 600; font-size: 21px; line-height: 1.1; color: var(--ink);
  }
  .person-role { font-size: 11.5px; color: var(--ink-soft); margin-top: 4px; }
  .contacts { position: absolute; left: 28px; top: 215px; list-style: none; }
  .contacts li {
    display: flex; align-items: center; height: 17.5px;
    font-size: 12.5px; color: var(--ink-soft);
  }
  .contacts svg { width: 11px; height: 11px; margin-right: 10px; fill: var(--ink); }
  .social {
    position: absolute; right: 28px; top: 250px;
    display: flex; align-items: center; font-size: 12.5px; color: var(--ink-soft);
  }
  .social-mark { width: 14px; height: 14px; border-radius: 2px; background: var(--ink); margin-right: 6px; }
</style>
</head>
<body>
<main class="canvas">
  <section class="card card-front" aria-label="Card front">
    <span class="brand-name-front">BildeVOLD</span>
  </section>

  <section class="card card-back" aria-label="Card back">
    <span class="brand-name-back">BildeVOLD</span>
    <span class="website">www.bildevold.example</span>

    <div class="person">
      <p class="person-name">Henrik Audun Strandvik</p>
      <p class="person-role">Managing Director &amp; Photographer</p>
    </div>

    <ul class="contacts">
      <li>
        <svg viewBox="0 0 12 12" aria-hidden="true"><path d="M3 0h6a1 1 0 0 1 1 1v10a1 1 0 0 1-1 1H3a1 1 0 0 1-1-1V1a1 1 0 0 1 1-1zm0.6 1.4v8h4.8v-8zM6 10.2a.6.6 0 1 0 0 1.2.6.6 0 0 0 0-1.2z"/></svg>
        +4791264085
      </li>
      <li>
        <svg viewBox="0 0 12 12" aria-hidden="true"><path d="M0 2h12v8H0zm1 1v.4l5 3.2 5-3.2V3zm0 1.6V9h10V4.6L6 7.8z"/></svg>
        post@bildevold.example
      </li>
      <li>
        <svg viewBox="0 0 12 12" aria-hidden="true"><path d="M6 0a4 4 0 0 1 4 4c0 3-4 8-4 8S2 7 2 4a4 4 0 0 1 4-4zm0 2.4a1.6 1.6 0 1 0 0 3.2 1.6 1.6 0 0 0 0-3.2z"/></svg>
        Kvernbakken9, 6040 Langevåg
      </li>
    </ul>

    <div class="social">
      <span class="social-mark" aria-hidden="true"></span>
      /BildeVOLD
    </div>
  </section>
</main>
</body>
</html>
```